Dunmore Roofing

Want a professional looking business card

Industry/Entity Type

Business

Contact Information for Business Card

Paul Dunmore ( Owner) paul@dunmoreroofing-example.com, www.dunmoreroofing-example.com, Adress: 4172 Township road 43 Plantagenet,ON K9X4T2

```html
<!DOCTYPE html>
<html lang="en">
<head>
<meta charset="utf-8">
<title>Dunmore Roofing — Business Card</title>
<link href="https://fonts.googleapis.com/css2?family=Source+Sans+3:wght@400;600;700&display=swap" rel="stylesheet">
<style>
  :root {
    --brand-blue: #1b4587;
    --brand-blue-soft: #244f93;
    --ink-grey: #58595b;
    --band-grey: #75777a;
    --rule-grey: #b9babc;
    --card-white: #ffffff;
    --backdrop: #e4e5e7;
  }
  * { box-sizing: border-box; margin: 0; padding: 0; }
  html, body {
    width: 1200px; height: 1080px; overflow: hidden;
    background: var(--backdrop);
    font-family: "Source Sans 3", Arial, sans-serif;
  }
  .sheet { position: relative; width: 1200px; height: 1080px; }
  .card {
    position: absolute; left: 220px; width: 760px; height: 434px;
    overflow: hidden;
  }

  /* Front side */
  .card--front { top: 70px; background: var(--brand-blue); }
  .front__map {
    position: absolute; left: 60px; top: 40px; width: 640px; height: 330px;
    border-radius: 40px;
    background: radial-gradient(ellipse at center, var(--brand-blue-soft) 0%, var(--brand-blue) 70%);
  }
  .front__name {
    position: absolute; left: 0; right: 0; top: 150px;
    text-align: center; color: var(--card-white);
    font-weight: 700; font-size: 58px; line-height: 1.05;
    letter-spacing: 4px; text-transform: uppercase;
  }
  .front__web {
    position: absolute; left: 0; right: 0; bottom: 40px;
    display: flex; align-items: center; justify-content: center; gap: 14px;
    color: var(--card-white); font-size: 19px;
  }
  .front__web .rule { height: 1px; width: 180px; background: linear-gradient(90deg, transparent, rgba(255,255,255,.85)); }
  .front__web .rule--right { background: linear-gradient(90deg, rgba(255,255,255,.85), transparent); }

  /* Back side */
  .card--back { top: 576px; background: var(--card-white); }
  .back__brand {
    position: absolute; left: 50px; top: 122px; width: 300px;
    color: var(--brand-blue); font-weight: 700; font-size: 42px; line-height: 1.05;
    letter-spacing: 2px; text-transform: uppercase; text-align: center;
  }
  .back__divider {
    position: absolute; left: 380px; top: 70px; width: 1px; height: 200px; background: var(--rule-grey);
  }
  .contact { position: absolute; left: 408px; top: 70px; color: var(--ink-grey); }
  .contact__name { color: var(--brand-blue); font-weight: 700; font-size: 26px; line-height: 1.1; }
  .contact__role { font-size: 19px; margin-top: 2px; }
  .contact__address { font-size: 19px; line-height: 1.3; margin-top: 14px; }
  .contact__list { list-style: none; margin-top: 12px; font-size: 19px; }
  .contact__list li { display: flex; align-items: center; gap: 9px; line-height: 1.45; }
  .icon { width: 20px; height: 20px; flex: none; }
  .back__band { position: absolute; left: 0; bottom: 0; width: 760px; height: 46px; }
</style>
</head>
<body>
<main class="sheet">
  <section class="card card--front" aria-label="Card front">
    <div class="front__map" role="img" aria-label="Faint dotted world map in deep blue"></div>
    <h1 class="front__name">Dunmore<br>Roofing</h1>
    <p class="front__web"><span class="rule"></span>www.dunmoreroofing-example.com<span class="rule rule--right"></span></p>
  </section>

  <section class="card card--back" aria-label="Card back">
    <p class="back__brand">Dunmore<br>Roofing</p>
    <div class="back__divider"></div>
    <div class="contact">
      <p class="contact__name">Paul Dunmore</p>
      <p class="contact__role">Owner</p>
      <p class="contact__address">4172 Township road 43,<br>Alderbrook, ON K9X4T2</p>
      <ul class="contact__list">
        <li>
          <svg class="icon" viewBox="0 0 20 20"><circle cx="10" cy="10" r="10" fill="var(--brand-blue)"/><path d="M7 5.5c.5-.4 1-.3 1.3.2l.8 1.6c.2.4 0 .8-.3 1l-.6.5c.4 1 1.2 1.9 2.2 2.4l.5-.6c.3-.3.7-.4 1-.2l1.6.9c.4.3.5.8.1 1.3l-.6.7c-.5.5-1.3.6-2 .3-2.3-1-4-2.8-4.9-5.1-.3-.7-.1-1.5.4-2z" fill="#fff"/></svg>
          (613) 555-0147
        </li>
        <li>
          <svg class="icon" viewBox="0 0 20 20"><circle cx="10" cy="10" r="10" fill="var(--brand-blue)"/><rect x="5" y="6.5" width="10" height="7" fill="none" stroke="#fff" stroke-width="1.2"/><path d="M5 6.5l5 4 5-4" fill="none" stroke="#fff" stroke-width="1.2"/></svg>
          paul@dunmoreroofing-example.com
        </li>
        <li>
          <svg class="icon" viewBox="0 0 20 20"><circle cx="10" cy="10" r="10" fill="var(--brand-blue)"/><circle cx="10" cy="10" r="5.5" fill="none" stroke="#fff" stroke-width="1.1"/><ellipse cx="10" cy="10" rx="2.4" ry="5.5" fill="none" stroke="#fff" stroke-width="1"/><path d="M4.5 10h11" stroke="#fff" stroke-width="1"/></svg>
          www.dunmoreroofing-example.com
        </li>
      </ul>
    </div>
    <svg class="back__band" viewBox="0 0 760 46" preserveAspectRatio="none">
      <polygon points="0,0 520,0 508,23 520,46 0,46" fill="var(--brand-blue)"/>
      <polygon points="534,0 760,0 760,46 534,46 522,23" fill="var(--band-grey)"/>
    </svg>
  </section>
</main>
</body>
</html>
```